Business Card Re-Design/Update

We'd like to update out business cards. I've included our current "Style guide" which has the colour scheme of the organisation in it. I've also included the branding files with logos etc in them.

I've also included a copy of one of our existing cards so that you can see how ugly/dated they look. I'd like a fresh modern corporate look.

Target Market(s)

These are for our clients, potential clients, industry contacts - like all business cards

Contact Information for Business Card

Name
Position
Company Address - Level 1, 47 Fernby Street, Carlow Qld 4072
Direct Phone
mobile
Email
Website -www.korvalit.com.au
Logo

Colors

Designer to choose colors to be used in the design.

Requirements
Must have
• Main Logo
• Cards will need to be editable to be able to personalize them for each new employee.
Nice to have
• The MapOut, ShipWell, KeepSteady would be okay to have if they can be sensibly and professionally added to the look without detracting from the main imagery.
• Maybe they could go on the back of the card? will leave this to your creative discretion as to whether/where they fit.
Should not have
• Should not have decorative or script fonts

```html
<!DOCTYPE html>
<html lang="en">
<head>
<meta charset="utf-8">
<title>Korval IT business card</title>
<link rel="stylesheet" href="https://fonts.googleapis.com/css2?family=Arimo:wght@400;700&display=swap">
<style>
  :root {
    --backdrop: #8f8f8f;
    --card-dark: #070707;
    --card-light: #eeeeee;
    --brand-red: #d3171f;
    --ink: #2a2a2a;
    --rule: #6b6b6b;
    --ship-blue: #2b8fd8;
    --keep-magenta: #c42a9c;
    --map-green: #6ab23e;
  }
  * { margin: 0; padding: 0; box-sizing: border-box; }
  html, body { width: 1064px; height: 1200px; overflow: hidden; }
  body {
    background: var(--backdrop);
    font-family: "Arimo", Arial, sans-serif;
    position: relative;
  }
  .card { position: absolute; height: 391px; }
  .card-back {
    left: 265px; top: 141px; width: 632px;
    background: var(--card-dark);
    border-radius: 0 196px 196px 0;
  }
  .card-front {
    left: 234px; top: 584px; width: 629px;
    background: var(--card-light);
    border-radius: 196px 0 0 196px;
  }
  .brand-name {
    position: absolute; left: 0; width: 576px; top: 126px;
    text-align: center;
    font-size: 52px; font-weight: 400; color: var(--brand-red);
    letter-spacing: -0.5px;
  }
  .divider {
    position: absolute; left: 55px; top: 263px; width: 468px;
    height: 1px; background: var(--rule);
  }
  .services {
    position: absolute; left: 0; width: 576px; top: 290px;
    display: flex; justify-content: center; gap: 22px;
  }
  .service {
    display: flex; align-items: center; gap: 7px;
    font-size: 25px; font-weight: 400;
  }
  .service-mark { width: 18px; height: 18px; }
  .service-ship { color: var(--ship-blue); }
  .service-ship .service-mark { background: var(--ship-blue); }
  .service-keep { color: var(--keep-magenta); }
  .service-keep .service-mark { background: var(--keep-magenta); }
  .service-map { color: var(--map-green); }
  .service-map .service-mark { background: var(--map-green); }

  .front-brand {
    position: absolute; left: 40px; width: 280px; top: 168px;
    text-align: center;
    font-size: 44px; font-weight: 700; color: var(--brand-red);
  }
  .details { position: absolute; left: 335px; top: 82px; color: var(--ink); }
  .person-name { font-size: 23px; font-weight: 700; color: var(--brand-red); line-height: 28px; }
  .person-role { font-size: 18px; line-height: 22px; }
  .contact-list { list-style: none; margin-top: 15px; }
  .contact-list li {
    display: flex; align-items: center; gap: 4px;
    font-size: 17px; line-height: 22.7px;
  }
  .contact-icon { width: 14px; height: 14px; flex: none; }
  .address { margin-top: 23px; font-size: 17px; line-height: 23px; }
</style>
</head>
<body>
  <section class="card card-back">
    <div class="brand-name">korvalIT</div>
    <div class="divider"></div>
    <div class="services">
      <span class="service service-ship"><span class="service-mark"></span>ShipWell</span>
      <span class="service service-keep"><span class="service-mark"></span>KeepSteady</span>
      <span class="service service-map"><span class="service-mark"></span>MapOut</span>
    </div>
  </section>

  <section class="card card-front">
    <div class="front-brand">korvalIT</div>
    <div class="details">
      <div class="person-name">Daniel Harper</div>
      <div class="person-role">Position</div>
      <ul class="contact-list">
        <li>
          <svg class="contact-icon" viewBox="0 0 14 14" aria-hidden="true">
            <rect x="3" y="1" width="8" height="12" rx="1.5" fill="none" stroke="#d3171f" stroke-width="1.8"/>
            <circle cx="7" cy="10.5" r="0.9" fill="#d3171f"/>
          </svg>401 732 58164
        </li>
        <li>
          <svg class="contact-icon" viewBox="0 0 14 14" aria-hidden="true">
            <path d="M1 5 Q7 1 13 5 L11.5 6.5 L9.5 5.5 L9.5 4.5 Q7 3.8 4.5 4.5 L4.5 5.5 L2.5 6.5 Z" fill="#d3171f"/>
            <rect x="3" y="7" width="8" height="5" rx="1" fill="#d3171f"/>
          </svg>401 732 58164
        </li>
        <li>
          <svg class="contact-icon" viewBox="0 0 14 14" aria-hidden="true">
            <rect x="1" y="3" width="12" height="8" fill="#d3171f"/>
            <path d="M1 3 L7 8 L13 3" fill="none" stroke="#eeeeee" stroke-width="1.2"/>
          </svg>hello@korvalit.com.au
        </li>
        <li>
          <svg class="contact-icon" viewBox="0 0 14 14" aria-hidden="true">
            <circle cx="7" cy="7" r="6" fill="#d3171f"/>
            <path d="M1 7 H13 M7 1 Q3.5 7 7 13 M7 1 Q10.5 7 7 13" fill="none" stroke="#eeeeee" stroke-width="0.9"/>
          </svg>www.korvalit.com.au
        </li>
      </ul>
      <p class="address">Level 1, 47 Fernby Street<br>Carlow Qld 4072</p>
    </div>
  </section>
</body>
</html>
```